Wordpress Design Project for Bankruptcy Law Office in San Francisco

our current website: www.dorvanelilaw-example.com

we would like to re-design it for wordpress to make it faster and a bit more modern.

content should be similar to what we have there right now but also we do family law

please include logo for law office:

Law Office of Marta K. Dolvenidze

Thank you.
Updates

please see attached word document with logos that we like as an example.

we do tend to like color red.  darker red.

Please submit your design variations and logo as soon as possible.   We would like to go over them and make our decision

Reason: Please create couple of more variations of logo for your design, so we can make our decision what we like the most. Please see word doc for samples: Text: Law Office Of Marta K. Dolvenidze

Reason: final touches

Target Market(s)

bankruptcy and family law clients

Industry/Entity Type

Family Law

Requirements
Must have
• see examples of law sites
http://promo.lexorbin-example.com/testimonials

- new logo: Law Office of Marta K. Dolvenidze
- client intake form
- blog
- contact us form

Nice to have
• - map
- red color
- on the front page a nice photo of SF or a happy family

```html
<!DOCTYPE html>
<html lang="en">
<head>
<meta charset="utf-8">
<title>Ledger Law 360 – Bankruptcy Information</title>
<link href="https://fonts.googleapis.com/css2?family=Source+Sans+3:ital,wght@0,400;0,600;0,700;1,400&display=swap" rel="stylesheet">
<style>
:root{
  --brand:#2f7fa8;
  --brand-dark:#1d4f6b;
  --nav-top:#3f93bb;
  --nav-bottom:#2a7096;
  --nav-line:#5aa6c9;
  --sidebar:#245f80;
  --sidebar-head:#1c4c67;
  --link:#2d7099;
  --ink:#1b1b1b;
  --body:#444;
  --band:#f3f3f3;
  --footer:#ebebeb;
  --button:#0f3048;
}
*{margin:0;padding:0;box-sizing:border-box}
html,body{width:712px;height:1200px;overflow:hidden;background:#fff}
body{font-family:"Source Sans 3",Arial,sans-serif;color:var(--body);position:relative}
.abs{position:absolute}
.top-rule{left:0;top:0;width:712px;height:3px;background:var(--brand-dark)}
/* header */
.brand{left:18px;top:28px}
.brand-mark{display:flex;align-items:center;gap:6px}
.brand-square{width:14px;height:14px;background:var(--brand)}
.brand-name{font-size:26px;font-weight:700;color:var(--brand);letter-spacing:-.5px;line-height:1}
.brand-sub{font-size:9px;color:var(--brand);margin-top:8px}
.lang{right:20px;top:18px;display:flex;align-items:center;gap:6px;font-size:8.5px;color:var(--link)}
.lang-box{width:77px;height:17px;background:#e4edf2;border:1px solid #cfdde5;font-size:8px;color:#333;padding:3px 6px;position:relative}
.lang-box svg{position:absolute;right:6px;top:6px}
.callus{right:20px;top:56px;font-size:11px;color:var(--link);letter-spacing:.3px}
.callus b{font-size:16px;color:#111;font-weight:400;margin-left:4px}
/* nav */
.nav{left:0;top:88px;width:712px;height:30px;background:linear-gradient(var(--nav-top),var(--nav-bottom));display:flex}
.nav a{display:block;height:30px;line-height:30px;color:#fff;font-size:9.6px;text-decoration:none;text-align:center;border-right:1px solid var(--nav-line)}
.nav a.current{background:var(--brand-dark)}
/* hero */
.hero{left:0;top:118px;width:712px;height:246px;background:linear-gradient(180deg,#d9d3c8 0%,#c8bfb2 55%,#6e6a66 100%)}
/* services */
.services{left:0;top:364px;width:712px;height:176px;background:var(--band)}
.service{width:162px;top:14px}
.service h3{font-size:11px;font-weight:600;color:var(--ink);margin-bottom:5px}
.service .thumb{height:66px;border:2px solid #fff;box-shadow:0 0 2px #bbb}
.service h4{font-size:9.5px;color:var(--brand-dark);font-weight:700;margin-top:7px}
.service p{font-size:7.8px;color:var(--link);line-height:1.55}
/* main column */
.main{left:12px;top:552px;width:468px}
.main h1{font-size:11px;font-weight:600;color:var(--ink);margin-bottom:9px}
.main p{font-size:7.9px;line-height:12.6px;margin-bottom:3px;color:var(--body)}
.main h5{font-size:7.9px;font-weight:700;color:var(--ink);margin:6px 0 3px}
.divider{left:12px;top:786px;width:474px;border-top:1px dotted #999}
.stories-head{left:16px;top:804px;font-size:11px;font-weight:600;color:var(--ink)}
.story-img{width:152px;height:100px}
.story{width:311px}
.story h4{font-size:9px;font-weight:600;color:var(--link);margin-bottom:3px}
.story p,.story-tail{font-size:7.9px;line-height:12.8px;color:var(--body);margin-bottom:3px}
.story-tail{width:470px}
/* sidebar */
.sidebar{left:506px;top:540px;width:206px;height:610px;background:var(--sidebar)}
.side-head{left:506px;width:206px;height:30px;background:var(--sidebar-head);color:#fff;font-size:11.5px;padding:8px 12px;font-variant:small-caps;letter-spacing:.3px;border-bottom:2px solid #2f7399}
.form{left:518px;top:576px;width:180px}
.form label{display:block;font-size:8px;line-height:9px;height:9px;color:#fff;margin-bottom:2px}
.form .field{height:17px;background:#fff;margin-bottom:6px}
.form .area{height:47px;background:#fff;margin-bottom:7px}
.form .check{font-size:7.5px;line-height:9px;color:#fff;display:flex;align-items:center;gap:6px;margin-left:1px}
.form .check span{width:8px;height:8px;background:#dfe8ee}
.btns{display:flex;gap:9px;margin-top:8px;margin-left:1px}
.btn{height:17px;padding:0 10px;background:var(--button);color:#fff;font-size:7.8px;font-weight:700;line-height:17px;border-radius:2px}
.news{left:519px;width:184px;color:#fff}
.news h4{font-size:9px;font-weight:400}
.news p{font-size:7.6px;font-style:italic;line-height:1.55}
.news a{display:block;font-size:7.8px;font-weight:700;color:#fff;text-decoration:none;margin-top:4px}
/* footer */
.footer{left:0;top:1150px;width:712px;height:50px;background:var(--footer)}
.foot-left{left:14px;top:1162px;font-size:7.6px;color:#333}
.foot-right{right:20px;top:1162px;font-size:7.6px;color:#333}
</style>
</head>
<body>
<div class="abs top-rule"></div>

<header>
  <div class="abs brand">
    <div class="brand-mark"><span class="brand-square"></span><span class="brand-name">LedgerLaw360</span></div>
    <div class="brand-sub">Law Office of Marta K. Dolvenidze</div>
  </div>
  <div class="abs lang">Select Language
    <div class="lang-box">English<svg width="6" height="4" viewBox="0 0 6 4"><path d="M0 0h6L3 4z" fill="#555"/></svg></div>
  </div>
  <div class="abs callus">CALL US NOW: <b>(555) 014-2290</b></div>
</header>

<nav class="abs nav">
  <a class="current" style="width:74px">HOME</a>
  <a style="width:80px">ABOUT US</a>
  <a style="width:115px">AREAS OF PRACTISE</a>
  <a style="width:89px">RESOURCES</a>
  <a style="width:55px">BLOG</a>
  <a style="width:49px">FAQ</a>
  <a style="width:92px;border-right:none">CONTACT US</a>
</nav>

<div class="abs hero" role="img" aria-label="Photo of a smiling legal team gathered around a meeting table in a bright office"></div>

<section class="abs services">
  <div class="abs service" style="left:14px">
    <h3>Debt Relief</h3>
    <div class="thumb" role="img" aria-label="Photo of a relieved man lying on grass among papers" style="background:linear-gradient(#9bb56a,#6f8f3d)"></div>
    <h4>Tittle goes here</h4>
    <p>Lorem ipsum dolor sit amet, consectetur adipisicing elit, sed do eiusmod tempor incididunt ut labore et dolore magna</p>
  </div>
  <div class="abs service" style="left:191px">
    <h3>Fore Closure Prevention</h3>
    <div class="thumb" role="img" aria-label="Photo of a for-sale sign on a white picket fence" style="background:linear-gradient(90deg,#5a5a5a,#c43a36 45%,#d9d9d9)"></div>
    <h4>Tittle goes here</h4>
    <p>Lorem ipsum dolor sit amet, consectetur adipisicing elit, sed do eiusmod tempor incididunt ut labore et dolore magna</p>
  </div>
  <div class="abs service" style="left:367px">
    <h3>Chapter 13</h3>
    <div class="thumb" role="img" aria-label="Photo of open law books on a desk" style="background:linear-gradient(#6b4a30,#c9b79a 55%,#8a5a36)"></div>
    <h4>Tittle goes here</h4>
    <p>Lorem ipsum dolor sit amet, consectetur adipisicing elit, sed do eiusmod tempor incididunt ut labore et dolore magna</p>
  </div>
  <div class="abs service" style="left:545px">
    <h3>Chapter 7</h3>
    <div class="thumb" role="img" aria-label="Photo of a row of leather-bound law books" style="background:linear-gradient(90deg,#3a2a20,#8a5a34,#2d211a)"></div>
    <h4>Tittle goes here</h4>
    <p>Lorem ipsum dolor sit amet, consectetur adipisicing elit, sed do eiusmod tempor incididunt ut labore et dolore magna</p>
  </div>
</section>

<main>
  <article class="abs main">
    <h1>WELCOME TO LEDGER LAW 360 - COMPLETE BANKRUPTCY INFORMATION</h1>
    <p>The Law Offices of Marta K. Dolvenidze is a consumer law office dedicated to consumer protection and zealously defending the rights of our clients. We offer the big firm quality legal representation with a small firm individualized attention to each client.</p>
    <p>Our office offers services in: all types of consumer bankruptcy filings, i.e. Chapter 7, Chapter 13, Chapter 11, negotiating a settlement of your debts, assisting you in the defense of collection litigation and defending you against foreclosure. Please review our site and see what we may be able to offer you. Feel free to call us at (555) 013-0411 or use our free case evaluation form.</p>
    <h5>Speak to a Lawyer</h5>
    <p>Unlike some other law firms, when you call the Law Office of Marta K. Dolvenidze you will speak to an actual attorney. Not a paralegal or assistant. And even after retaining our office you will still speak to an attorney unlike other firms where you cannot get a hold of your attorney after several attempts.</p>
    <p style="margin-top:8px">Lorem ipsum dolor sit amet, consectetuer adipiscing elit. Nam cursus. Morbi ut mi. Nullam enim leo, egestas id, condimentum at, laoreet mattis, massa. Sed eleifend nonummy diam. Praesent mauris ante, elementum et, bibendum at, posuere sit amet, nibh. Duis tincidunt lectus quis dui viverra vestibulum. Suspendisse vulputate aliquam dui. Nulla elementum dui ut augue. Aliquam vehicula mi at mauris. Maecenas placerat, nisl at consequat rhoncus, sem nunc gravida justo, quis eleifend arcu velit quis lacus. Morbi magna magna, tincidunt a, mattis non, imperdiet vitae</p>
  </article>

  <div class="abs divider"></div>
  <h2 class="abs stories-head">STORIES &amp; MORE INFORMATION</h2>

  <div class="abs story-img" style="left:13px;top:830px;background:linear-gradient(135deg,#2a140c,#8a4a26 55%,#3a1c10)" role="img" aria-label="Photo of a wooden gavel resting on a law book"></div>
  <div class="abs story" style="left:174px;top:828px">
    <h4>Story TItle line goes here</h4>
    <p>Lorem ipsum dolor sit amet, consectetuer adipiscing elit. Nam cursus. Morbi ut mi. Nullam enim leo, egestas id, condimentum at, laoreet mattis, massa.</p>
    <p>Sed eleifend nonummy diam. Praesent mauris ante, elementum et, bibendum at, posuere sit amet, nibh. Duis tincidunt lectus quis dui viverra vestibulum. Suspendisse vulputate aliquam dui. Nulla elementum dui ut augue. Aliquam vehicula mi at mauris. Maecenas placerat, nisl at consequat rhoncus, sem nunc gravida justo, quis eleifend arcu velit quis lacus. Morbi magna magna, tincidunt a, mattis non, imperdiet vitae, tellus.</p>
  </div>
  <p class="abs story-tail" style="left:13px;top:942px">Mauris vel lacus vitae felis vestibulum volutpat. Etiam est nunc, venenatis in, tristique eu, imperdiet ac, nisl. Cum sociis natoque penatibus et magnis dis parturient montes, nascetur ridiculus mus. In iaculis facilisis massa.</p>

  <div class="abs story-img" style="left:11px;top:986px;width:157px;background:linear-gradient(160deg,#a9c27a,#c8a088 50%,#6f8f4a)" role="img" aria-label="Photo of a happy family with children on bicycles in a park"></div>
  <div class="abs story" style="left:178px;top:985px;width:308px">
    <h4>Story TItle line goes here</h4>
    <p>Lorem ipsum dolor sit amet, consectetuer adipiscing elit. Nam cursus. Morbi ut mi. Nullam enim leo, egestas id, condimentum at, laoreet mattis, massa.</p>
    <p>Sed eleifend nonummy diam. Praesent mauris ante, elementum et, bibendum at, posuere sit amet, nibh. Duis tincidunt lectus quis dui viverra vestibulum. Suspendisse vulputate aliquam dui. Nulla elementum dui ut augue. Aliquam vehicula mi at mauris. Maecenas placerat, nisl at consequat rhoncus, sem nunc gravida justo, quis eleifend arcu velit quis lacus. Morbi magna magna, tincidunt a, mattis non, imperdiet vitae, tellus.</p>
  </div>
  <p class="abs story-tail" style="left:11px;top:1099px">Mauris vel lacus vitae felis vestibulum volutpat. Etiam est nunc, venenatis in, tristique eu, imperdiet ac, nisl. Cum sociis natoque penatibus et magnis dis parturient montes, nascetur ridiculus mus. In iaculis facilisis massa.</p>
</main>

<aside>
  <div class="abs sidebar"></div>
  <div class="abs side-head" style="top:540px">Contact Form</div>
  <form class="abs form">
    <label>Name:</label><div class="field"></div>
    <label>Email:</label><div class="field"></div>
    <label>Phone:</label><div class="field"></div>
    <label>Subject:</label><div class="field"></div>
    <label>Message:</label><div class="area"></div>
    <div class="check"><span></span>Send a copy of this message to yourself</div>
    <div class="btns"><div class="btn">SEND</div><div class="btn">RESET</div></div>
  </form>

  <div class="abs side-head" style="top:826px">Recent Blog &amp; News</div>
  <div class="abs news" style="top:867px">
    <h4>Title line here</h4>
    <p>Lorem ipsum dolor sit amet, consectetuer adipiscing elit. Nam cursus. Morbi ut mi. Nullam enim leo, egestas id, condimentum at, laoreet mattis, massa.</p>
    <a>LEARN MORE</a>
  </div>
  <div class="abs news" style="top:940px">
    <h4>Title line here</h4>
    <p>Lorem ipsum dolor sit amet, consectetuer adipiscing elit. Nam cursus. Morbi ut mi. Nullam enim leo, egestas id, condimentum at, laoreet mattis, massa.</p>
    <a>LEARN MORE</a>
  </div>
  <div class="abs news" style="top:1014px">
    <h4>Title line here</h4>
    <p>Proin dui lectus, cursus eu, mattis laoreet, viverra sit amet, quam. Curabitur vel dolor ultrices ipsum dictum tristique. Praesent vitae lacus. Ut velit enim, vestibulum non, fermentum nec, hendrerit quis, leo. Pellentesque rutrum malesuada neque.</p>
    <a>LEARN MORE</a>
  </div>
</aside>

<footer>
  <div class="abs footer"></div>
  <div class="abs foot-left">© 2012 Company Name &nbsp;|&nbsp; All right reserved &nbsp;|&nbsp; Term &amp; Conditions</div>
  <div class="abs foot-right">HOME &nbsp;|&nbsp; ABOUT US &nbsp;|&nbsp; AREAS OF PRACTISE &nbsp;|&nbsp; RESOURCES &nbsp;|&nbsp; BLOG &nbsp;|&nbsp; FAQ &nbsp;|&nbsp; CONTACT US</div>
</footer>
</body>
</html>
```